Elegant Business Card for Technology Company

Client is a supplier of innovative industrial communications and automation equipment since 2002. This contest is to gather fresh ideas for a redesign of the existing business card. Client is looking for design that best communicates tagline "Industrial Networking and Computing Specialist".

Design submissions should look modern, clean, elegant and professional. It should not be cluttered. Use white as the primary colour. Orange and black as secondary colour. Refer to jpeg File 1 on the current design.

Fonts used by Client used include Arial Regular, Arial Black, Roboto Regular, Roboto Black and Lato.

The winning design will be sent for offset printing using super white 250gsm artcard paper (open for suggestions).

Target Market(s)

System Engineers, Project Managers, Purchasing Managers from companies providing engineering services for Smart Cities.

Industry/Entity Type

Information Technology

Contact Information for Business Card

Refer to PDF File 3 for Business Card Details. Priority of short contact information would be as follows Name > Job Title > Email > Mobile > Web > Tel > Fax > Business Address >UEN (UEN represents company registration number)

Font styles to use
Sans Serif

Colors
ffffff
f37122
000000
5c5c5c

Requirements
Must have
• Refer to AI File 2 (Company Logo) & PDF File 3 (Information on Namecard)
Should not have
• No QR codes
• No Social Media Icons
• Do not create full Black or Orange colour background

```html
<!DOCTYPE html>
<html lang="en">
<head>
<meta charset="utf-8">
<title>VEXA business card</title>
<link rel="stylesheet" href="https://fonts.googleapis.com/css2?family=Source+Sans+3:wght@400;600;800&display=swap">
<style>
  :root {
    --white: #ffffff;
    --orange: #f37122;
    --black: #000000;
    --grey: #5c5c5c;
    --rule: #d4d4d4;
    --backdrop: #8e8e8e;
    --font: "Source Sans 3", Arial, sans-serif;
  }
  * { margin: 0; padding: 0; box-sizing: border-box; }
  html, body { width: 1105px; height: 1200px; overflow: hidden; }
  body { background: var(--backdrop); font-family: var(--font); position: relative; }

  .card { position: absolute; left: 182px; width: 746px; height: 425px; overflow: hidden; background: var(--white); }
  .card-front { top: 119px; }
  .card-back { top: 636px; }

  /* front */
  .brand { position: absolute; left: 74px; top: 170px; display: flex; align-items: center; gap: 16px; }
  .brand-dot { width: 64px; height: 64px; border-radius: 50%; background: var(--orange); }
  .brand-name { font-weight: 800; font-size: 72px; line-height: 1; color: var(--black); letter-spacing: 1px; }

  .divider { position: absolute; left: 388px; top: 40px; width: 1px; height: 322px; background: var(--rule); }

  .details { position: absolute; left: 418px; top: 50px; color: var(--grey); }
  .person-name { font-size: 28px; font-weight: 600; color: var(--orange); line-height: 1.1; }
  .person-title { font-size: 20px; color: var(--black); margin-top: 2px; }
  .address { font-size: 20px; line-height: 27px; margin-top: 12px; }
  .contacts { list-style: none; margin-top: 4px; }
  .contacts li { display: flex; align-items: center; gap: 10px; font-size: 20px; line-height: 28.5px; }
  .contacts svg { width: 18px; height: 18px; fill: var(--orange); flex: none; }

  .accent-line { position: absolute; left: 0; top: 386px; width: 100%; height: 3px; background: var(--orange); }
  .base-band { position: absolute; left: 0; top: 392px; width: 100%; height: 33px; background: var(--black); }

  /* back */
  .top-band { position: absolute; left: 0; top: 0; width: 100%; height: 20px; background: var(--black); }
  .top-accent { position: absolute; left: 0; top: 23px; width: 100%; height: 3px; background: var(--orange); }
  .back-brand { position: absolute; left: 0; right: 0; top: 120px; text-align: center; font-weight: 800; font-size: 88px; line-height: 1; color: var(--black); letter-spacing: 2px; }
  .tagline { position: absolute; left: 0; right: 0; top: 290px; text-align: center; color: var(--grey); font-size: 20px; line-height: 26px; }
  .tagline-lead { color: var(--orange); font-weight: 600; }
</style>
</head>
<body>

<section class="card card-front">
  <div class="brand">
    <span class="brand-dot"></span>
    <span class="brand-name">VEXA</span>
  </div>
  <div class="divider"></div>
  <div class="details">
    <p class="person-name">Daniel Lim</p>
    <p class="person-title">Sales Manager</p>
    <p class="address">27 Kallan Way Loop<br>Innopark #05-12 (Block B)<br>Singapore 409921</p>
    <ul class="contacts">
      <li><svg viewBox="0 0 24 24"><path d="M6.6 10.8a15.1 15.1 0 0 0 6.6 6.6l2.2-2.2c.3-.3.7-.4 1-.2 1.1.4 2.3.6 3.6.6.6 0 1 .4 1 1V20c0 .6-.4 1-1 1A17 17 0 0 1 3 4c0-.6.4-1 1-1h3.5c.6 0 1 .4 1 1 0 1.3.2 2.5.6 3.6.1.3 0 .7-.2 1z"/></svg>+65 6000 1234</li>
      <li><svg viewBox="0 0 24 24"><path d="M7 1h10a2 2 0 0 1 2 2v18a2 2 0 0 1-2 2H7a2 2 0 0 1-2-2V3a2 2 0 0 1 2-2zm0 3v14h10V4zm5 15.5a1.2 1.2 0 1 0 0 2.4 1.2 1.2 0 0 0 0-2.4z"/></svg>+65 9000 5678</li>
      <li><svg viewBox="0 0 24 24"><path d="M7 2h10v5H7zM3 8h18a2 2 0 0 1 2 2v7h-4v5H5v-5H1v-7a2 2 0 0 1 2-2zm4 7v5h10v-5z"/></svg>+65 6000 4321</li>
      <li><svg viewBox="0 0 24 24"><path d="M2 5h20v14H2zm2 2v.5l8 5 8-5V7z"/></svg>sales@vexa-example.sg</li>
      <li><svg viewBox="0 0 24 24"><path d="M12 2a10 10 0 1 0 0 20 10 10 0 0 0 0-20zm-1 17.9A8 8 0 0 1 4.2 10L9 14.8v1a2 2 0 0 0 2 2zm6.9-2.5A2 2 0 0 0 16 16h-1v-3a1 1 0 0 0-1-1H8v-2h2a1 1 0 0 0 1-1V7h2a2 2 0 0 0 2-2v-.4a8 8 0 0 1 2.9 12.8z"/></svg>www.vexa-example.sg</li>
    </ul>
  </div>
  <div class="accent-line"></div>
  <div class="base-band"></div>
</section>

<section class="card card-back">
  <div class="top-band"></div>
  <div class="top-accent"></div>
  <div class="back-brand">VEXA</div>
  <p class="tagline"><span class="tagline-lead">Industrial Networking &amp; Computing Specialist</span><br>Industrial Ethernet / Wireless / Cellular<br>Industrial &amp; Embedded Computing / Serial / Fieldbus Connectivity<br>IP Video Surveillance / Remote Automation</p>
</section>

</body>
</html>
```